Seed Oil Safety Card for Healthy Restaurant Dining

I am seeking a design for a physical card to communicate my wife's health-related dietary restriction regarding seed oils. This card will be given to restaurant waiters to ensure her meals are prepared without seed oils, as it is a health issue and not merely a preference.
My wife cannot eat any “seed oil” or “processed oil”, including:
- Vegetable oil
- Canola oil
- Soybean oil
- Sunflower oil
- Corn oil
- Cottonseed oil
- Safflower oil
- Peanut oil
- Sesame oil
Oils that are OK for her to consume:
- Butter (most preferable)
- Extra virgin olive oil
- Avocado oil
- Coconut oil
- Ghee
- Lard
- Any other animal-based fats
Key Design Requirements:
- Clarity and speed of communication: The card should be easily read and understood by waiters, even in low-light environments, emphasizing that it's a health concern.
- Avoid common misconceptions: Ensure the design doesn't imply common dietary preferences like "vegetarian" or "no butter." Animal fats and butter are actually preferable for her!
- Preferred term: Use "seed oils" as the term to describe what she cannot eat due to her health issue.
- Trace amounts are acceptable: Communicate that it's OK to use cookware that has previously been in contact with seed oils, but not to have seed oil as an ingredient. Please suggest a concise way to convey this.
- Card dimensions: Design should be 3.5” x 2.25” (standard credit-card size on printorvale.example). Horizontal or vertical layouts are both fine, whichever makes the message clearer.
Design Suggestions:
- Utilize bold and easy-to-read typography to communicate the main message.
- Consider incorporating relevant icons or graphics that help convey the message without adding confusion.
- Use contrasting colors to enhance readability, especially in low-light situations.
- To communicate the “trace amounts OK” part, consider phrases such as:
- "Cross-contamination acceptable"
- “Used cookware OK, no ingredient use”
- “Separate cookware not necessary”
Thank you for your assistance in creating this essential card for my wife's health and safety when dining out!

```html
<!DOCTYPE html>
<html lang="en">
<head>
<meta charset="utf-8">
<title>Medical Dietary Restriction Card</title>
<link rel="stylesheet" href="https://fonts.googleapis.com/css2?family=Lato:ital,wght@0,400;0,700;0,900;1,400&display=swap">
<style>
  :root {
    --bg: #e1e2e4;
    --brand-blue: #1f6db4;
    --brand-blue-dark: #175a98;
    --card-white: #f4f6f8;
    --card-mist: #e3e7ec;
    --no-red: #c8202f;
    --ok-green: #3d8b2c;
    --ink: #1d1d1f;
    --footer-ink: #ffffff;
  }
  * { margin: 0; padding: 0; box-sizing: border-box; }
  html, body { width: 1200px; height: 2743px; overflow: hidden; }
  body {
    background: var(--bg);
    font-family: "Lato", Arial, sans-serif;
    position: relative;
  }
  .card {
    position: absolute;
    left: 222px; top: 786px;
    width: 755px; height: 1171px;
    border-radius: 42px;
    overflow: hidden;
    background: linear-gradient(160deg, var(--card-white) 0%, #ffffff 35%, var(--card-mist) 70%, #f7f8fa 100%);
    box-shadow: 14px 22px 30px rgba(0,0,0,0.28);
  }
  .card-header {
    position: absolute; left: 0; top: 0; width: 100%; height: 230px;
  }
  .card-header svg { position: absolute; left: 0; top: 0; }
  .header-kicker, .header-title {
    position: absolute; left: 0; width: 100%; text-align: center; color: #fff;
  }
  .header-kicker {
    top: 38px; font-size: 44px; font-weight: 400; letter-spacing: 9px; padding-left: 9px;
  }
  .header-title {
    top: 95px; font-size: 53px; font-weight: 900; letter-spacing: 0.5px;
  }
  .divider {
    position: absolute; left: 373px; top: 230px; width: 6px; height: 727px;
    background: var(--brand-blue);
  }
  .column { position: absolute; top: 237px; }
  .column-avoid { left: 0; width: 373px; }
  .column-allow { left: 379px; width: 376px; }
  .status-icon { display: block; margin: 0 auto; width: 90px; height: 90px; }
  .column-heading {
    margin-top: 52px; text-align: center; color: var(--ink);
    font-size: 36px; font-weight: 700; line-height: 40px; letter-spacing: 0.5px;
  }
  .oil-list { list-style: none; margin-top: 22px; }
  .column-avoid .oil-list { padding-left: 40px; color: var(--no-red); }
  .column-allow .oil-list { padding-left: 37px; color: var(--ok-green); }
  .oil-list li {
    position: relative; padding-left: 32px;
    font-size: 40px; line-height: 46.5px; font-weight: 400;
  }
  .oil-list li svg { position: absolute; left: 0; top: 14px; width: 20px; height: 20px; }
  .emblem {
    position: absolute; left: 505px; top: 1040px; width: 230px; height: 220px;
    border-radius: 40px;
    background: radial-gradient(circle, rgba(200,210,222,0.45) 0%, rgba(200,210,222,0) 70%);
  }
  .footnote {
    position: absolute; left: 45px; top: 1002px;
    font-size: 33px; font-style: italic; line-height: 38px; color: var(--ink);
  }
  .footnote .second { padding-left: 14px; }
  .card-footer {
    position: absolute; left: 0; bottom: 0; width: 100%; height: 66px;
    background: var(--brand-blue);
    color: var(--footer-ink); text-align: center;
    font-size: 26px; font-weight: 900; letter-spacing: 4px; line-height: 66px;
  }
</style>
</head>
<body>
  <article class="card">
    <header class="card-header">
      <svg width="755" height="230" viewBox="0 0 755 230" aria-hidden="true">
        <path d="M0 0 H755 V180 C600 170 480 140 300 150 C170 158 70 185 0 215 Z" fill="var(--brand-blue)"/>
      </svg>
      <div class="header-kicker">MEDICAL</div>
      <div class="header-title">DIETARY RESTRICTION</div>
    </header>

    <div class="emblem" role="img" aria-label="Faint medical star emblem decoration"></div>

    <div class="divider"></div>

    <section class="column column-avoid">
      <svg class="status-icon" viewBox="0 0 90 90" aria-hidden="true">
        <circle cx="45" cy="45" r="45" fill="var(--no-red)"/>
        <path d="M29 29 L61 61 M61 29 L29 61" stroke="#fff" stroke-width="11" stroke-linecap="round"/>
      </svg>
      <h2 class="column-heading">I CANNOT EAT<br>PROCESSED<br>SEED OILS</h2>
      <ul class="oil-list">
        <li><svg viewBox="0 0 20 20"><rect x="1" y="1" width="18" height="18" fill="none" stroke="currentColor" stroke-width="2"/><path d="M5 5 L15 15 M15 5 L5 15" stroke="currentColor" stroke-width="2.5"/></svg>Vegetable oil</li>
        <li><svg viewBox="0 0 20 20"><rect x="1" y="1" width="18" height="18" fill="none" stroke="currentColor" stroke-width="2"/><path d="M5 5 L15 15 M15 5 L5 15" stroke="currentColor" stroke-width="2.5"/></svg>Canola oil</li>
        <li><svg viewBox="0 0 20 20"><rect x="1" y="1" width="18" height="18" fill="none" stroke="currentColor" stroke-width="2"/><path d="M5 5 L15 15 M15 5 L5 15" stroke="currentColor" stroke-width="2.5"/></svg>Soybean oil</li>
        <li><svg viewBox="0 0 20 20"><rect x="1" y="1" width="18" height="18" fill="none" stroke="currentColor" stroke-width="2"/><path d="M5 5 L15 15 M15 5 L5 15" stroke="currentColor" stroke-width="2.5"/></svg>Sunflower oil</li>
        <li><svg viewBox="0 0 20 20"><rect x="1" y="1" width="18" height="18" fill="none" stroke="currentColor" stroke-width="2"/><path d="M5 5 L15 15 M15 5 L5 15" stroke="currentColor" stroke-width="2.5"/></svg>Corn oil</li>
        <li><svg viewBox="0 0 20 20"><rect x="1" y="1" width="18" height="18" fill="none" stroke="currentColor" stroke-width="2"/><path d="M5 5 L15 15 M15 5 L5 15" stroke="currentColor" stroke-width="2.5"/></svg>Cottonseed oil</li>
        <li><svg viewBox="0 0 20 20"><rect x="1" y="1" width="18" height="18" fill="none" stroke="currentColor" stroke-width="2"/><path d="M5 5 L15 15 M15 5 L5 15" stroke="currentColor" stroke-width="2.5"/></svg>Safflower oil</li>
        <li><svg viewBox="0 0 20 20"><rect x="1" y="1" width="18" height="18" fill="none" stroke="currentColor" stroke-width="2"/><path d="M5 5 L15 15 M15 5 L5 15" stroke="currentColor" stroke-width="2.5"/></svg>Peanut oil</li>
        <li><svg viewBox="0 0 20 20"><rect x="1" y="1" width="18" height="18" fill="none" stroke="currentColor" stroke-width="2"/><path d="M5 5 L15 15 M15 5 L5 15" stroke="currentColor" stroke-width="2.5"/></svg>Sesame oil</li>
      </ul>
    </section>

    <section class="column column-allow">
      <svg class="status-icon" viewBox="0 0 90 90" aria-hidden="true">
        <circle cx="45" cy="45" r="45" fill="var(--ok-green)"/>
        <path d="M25 46 L39 60 L66 31" fill="none" stroke="#fff" stroke-width="11" stroke-linecap="round" stroke-linejoin="round"/>
      </svg>
      <h2 class="column-heading">NATURAL OILS<br>&amp; FATS ARE<br>ACCEPTABLE</h2>
      <ul class="oil-list">
        <li><svg viewBox="0 0 20 20"><rect x="1" y="1" width="18" height="18" fill="none" stroke="currentColor" stroke-width="2"/><path d="M4.5 10 L8.5 14 L15.5 6" fill="none" stroke="currentColor" stroke-width="2.5"/></svg>Butter</li>
        <li><svg viewBox="0 0 20 20"><rect x="1" y="1" width="18" height="18" fill="none" stroke="currentColor" stroke-width="2"/><path d="M4.5 10 L8.5 14 L15.5 6" fill="none" stroke="currentColor" stroke-width="2.5"/></svg>Extra virgin<br>olive oil</li>
        <li><svg viewBox="0 0 20 20"><rect x="1" y="1" width="18" height="18" fill="none" stroke="currentColor" stroke-width="2"/><path d="M4.5 10 L8.5 14 L15.5 6" fill="none" stroke="currentColor" stroke-width="2.5"/></svg>Avocado oil</li>
        <li><svg viewBox="0 0 20 20"><rect x="1" y="1" width="18" height="18" fill="none" stroke="currentColor" stroke-width="2"/><path d="M4.5 10 L8.5 14 L15.5 6" fill="none" stroke="currentColor" stroke-width="2.5"/></svg>Coconut oil</li>
        <li><svg viewBox="0 0 20 20"><rect x="1" y="1" width="18" height="18" fill="none" stroke="currentColor" stroke-width="2"/><path d="M4.5 10 L8.5 14 L15.5 6" fill="none" stroke="currentColor" stroke-width="2.5"/></svg>Ghee</li>
        <li><svg viewBox="0 0 20 20"><rect x="1" y="1" width="18" height="18" fill="none" stroke="currentColor" stroke-width="2"/><path d="M4.5 10 L8.5 14 L15.5 6" fill="none" stroke="currentColor" stroke-width="2.5"/></svg>Lard</li>
        <li><svg viewBox="0 0 20 20"><rect x="1" y="1" width="18" height="18" fill="none" stroke="currentColor" stroke-width="2"/><path d="M4.5 10 L8.5 14 L15.5 6" fill="none" stroke="currentColor" stroke-width="2.5"/></svg>Natural animal<br>fats</li>
      </ul>
    </section>

    <p class="footnote">*Trace amounts acceptable<br><span class="second">Reuse cookwares acceptable</span></p>

    <footer class="card-footer">THANK YOU FOR KEEPING ME SAFE</footer>
  </article>
</body>
</html>
```